Business Card Design

We like to use greens as you will see in our logo (but not TOO much green). We are a Dental Clinic in a somewhat eccentric community. We do not like the dated sharp designs which we see many dentists use. We're looking for something bright and fresh while still maintaining the integrity of the profession. Elegance is not necessarily what we are going for... we need for the design to be "mature" but also up-lifting.

See our logo.
Updates

Project Deadline Extended
Reason: We have 5 designs which we like. But we'd like to see a few more before committing to a design.

Project Deadline Extended
Reason: We are awaiting revisions to this project. We are still welcoming designs while we wait to see if designers are able to provide to us the revisions we require in order to proceed with a selection.

Target Market(s)

Younger families - ages late 20's to early 40's

Industry/Entity Type

Business

Contact Information for Business Card

Corwel T. Banfry DDS 2730 W. Halvert Rd. Ste. 7 Fernmoor, OR 48391 (248)555-0174 FX (248)555-0189 info@BrightwellDentalCareMi.com BrigthwellDentalCareMi.com on the back of the card we need an appointment reminder (For____ Date___ Time____) with "If you are unable to keep your appointment, kindly give 48 hours notice" at the bottom. No use of teeth in the design. DOUBLE SIDED DESIGN

Requirements
Should not have
• The use of pictures of teeth

```html
<!DOCTYPE html>
<html lang="en">
<head>
<meta charset="utf-8">
<title>Brightwell Dental Care – Business Card</title>
<link rel="stylesheet" href="https://fonts.googleapis.com/css2?family=Open+Sans:wght@400;600;700;800&family=Tinos:ital,wght@0,700;1,400&display=swap">
<style>
  :root {
    --backdrop: #ece8e2;
    --card: #ffffff;
    --green-dark: #2f7d14;
    --green-mid: #5aa21c;
    --lime: #b6e02a;
    --lime-light: #e3f59a;
    --ink: #333333;
    --ink-soft: #555555;
    --box-line: #4a4a4a;
  }
  * { box-sizing: border-box; margin: 0; padding: 0; }
  html, body { width: 1200px; height: 492px; overflow: hidden; }
  body {
    background: var(--backdrop);
    font-family: "Open Sans", Arial, sans-serif;
    color: var(--ink);
    position: relative;
  }
  .card {
    position: absolute;
    top: 96px;
    width: 530px;
    height: 300px;
    background: var(--card);
    border-radius: 26px;
    overflow: hidden;
    box-shadow: 0 6px 18px rgba(0,0,0,.18);
  }
  .card--front { left: 55px; }
  .card--back { left: 615px; }

  /* Shared brand name */
  .brand {
    position: absolute;
    color: var(--green-dark);
    font-weight: 600;
    line-height: 1.05;
  }
  .brand__dot {
    display: inline-block;
    width: 16px; height: 16px;
    border-radius: 50%;
    background: var(--lime);
    margin-right: 6px;
    vertical-align: middle;
  }

  /* Front */
  .card--front .brand {
    left: 34px; top: 100px; width: 220px;
    font-size: 34px;
  }
  .divider {
    position: absolute;
    left: 262px; top: 40px;
    width: 2px; height: 150px;
    background: var(--lime);
  }
  .doctor {
    position: absolute;
    left: 282px; top: 42px;
    font-size: 19px; font-weight: 800;
    color: var(--green-dark);
  }
  .doctor small { font-size: 13px; font-weight: 700; }
  .contacts {
    position: absolute;
    left: 282px; top: 92px;
    list-style: none;
    font-size: 14px; color: var(--ink);
  }
  .contacts li { display: flex; align-items: center; gap: 5px; height: 21px; }
  .contacts svg { width: 12px; height: 12px; flex: none; }
  .address-band {
    position: absolute;
    left: 0; right: 0; bottom: 0;
    height: 70px;
  }
  .address-band svg { position: absolute; inset: 0; width: 100%; height: 100%; }
  .address {
    position: absolute;
    left: 0; right: 0; bottom: 14px;
    text-align: center;
    font-size: 14px; color: var(--ink);
  }

  /* Back */
  .card--back .brand {
    left: 24px; top: 30px; font-size: 22px;
  }
  .appointment-title {
    position: absolute;
    left: 26px; top: 92px;
    font-family: "Tinos", "Times New Roman", serif;
    font-weight: 700; font-size: 16px;
    color: var(--green-mid);
    letter-spacing: .3px;
  }
  .title-rule {
    position: absolute;
    left: 222px; top: 106px; width: 150px;
    border-top: 1px dotted var(--ink-soft);
  }
  .field { position: absolute; font-size: 15px; color: var(--ink); display: flex; align-items: flex-end; gap: 6px; }
  .field__line { display: inline-block; border-bottom: 1px solid var(--ink-soft); height: 1px; margin-bottom: 4px; }
  .field__line--dotted { border-bottom-style: dotted; }
  .box { display: inline-block; border: 1.5px solid var(--box-line); border-radius: 3px; background: #fff; }
  .box--time { position: absolute; left: 312px; top: 152px; width: 92px; height: 22px; }
  .days {
    position: absolute; left: 26px; top: 232px;
    display: flex; align-items: center; gap: 6px;
    font-size: 14px; font-weight: 700; color: var(--ink-soft);
  }
  .days .box { width: 30px; height: 20px; margin-right: 6px; }
  .notice {
    position: absolute; left: 26px; bottom: 20px;
    font-family: "Tinos", "Times New Roman", serif;
    font-style: italic; font-size: 15px; color: var(--ink-soft);
  }
</style>
</head>
<body>

<section class="card card--front" aria-label="Front of business card">
  <div class="brand"><span class="brand__dot"></span>Brightwell<br>Dental Care</div>
  <div class="divider"></div>
  <h1 class="doctor">Corwel T. Banfry, <small>DDS</small></h1>
  <ul class="contacts">
    <li><svg viewBox="0 0 12 12"><circle cx="6" cy="6" r="5.5" fill="none" stroke="#333"/><path d="M4 3.2 5 3l.6 1.6-.7.6a4 4 0 0 0 1.8 1.8l.6-.7L9 7l-.2 1A3.8 3.8 0 0 1 4 3.2z" fill="#333"/></svg>(503)555-0174</li>
    <li><svg viewBox="0 0 12 12"><rect x="2" y="1" width="8" height="4" fill="#333"/><rect x="0.5" y="5" width="11" height="6" rx="1" fill="#333"/><rect x="3" y="7" width="6" height="2" fill="#fff"/></svg>(503)555-0189</li>
    <li><svg viewBox="0 0 12 12"><rect x="0.5" y="2" width="11" height="8" rx="1" fill="#333"/><path d="M1 2.5 6 7l5-4.5" fill="none" stroke="#fff"/></svg>info@BrightwellDentalCareMi.com</li>
    <li><svg viewBox="0 0 12 12"><circle cx="6" cy="6" r="5.5" fill="#333"/><path d="M.5 6h11M6 .5v11M2 3.2h8M2 8.8h8" stroke="#fff" stroke-width=".7"/><ellipse cx="6" cy="6" rx="2.4" ry="5.5" fill="none" stroke="#fff" stroke-width=".7"/></svg>www.BrigthwellDentalCareMi.com</li>
  </ul>
  <div class="address-band">
    <svg viewBox="0 0 530 70" preserveAspectRatio="none" aria-hidden="true">
      <defs>
        <linearGradient id="band" x1="0" x2="1" y1="0" y2="0">
          <stop offset="0" stop-color="#e3f59a"/>
          <stop offset="1" stop-color="#b6e02a"/>
        </linearGradient>
      </defs>
      <path d="M0 40 Q270 30 530 0 V70 H0 Z" fill="url(#band)"/>
    </svg>
    <p class="address">2730 W. Halvert Rd. Ste. 7 Fernmoor, OR 48391</p>
  </div>
</section>

<section class="card card--back" aria-label="Back of business card, appointment reminder">
  <div class="brand"><span class="brand__dot"></span>Brightwell<br>Dental Care</div>
  <h2 class="appointment-title">YOUR APPOINTMENT</h2>
  <span class="title-rule"></span>

  <div class="field" style="left:26px; top:120px;">Name : <span class="field__line field__line--dotted" style="width:240px"></span>am / pm</div>
  <div class="field" style="left:26px; top:156px;">Date : <span class="field__line" style="width:80px"></span>&nbsp;Time : <span class="field__line" style="width:80px"></span></div>
  <span class="box box--time"></span>
  <div class="field" style="left:26px; top:194px;">Next Appointment <span class="box" style="width:92px; height:22px; margin-bottom:2px;"></span></div>

  <div class="days">
    MON <span class="box"></span>
    TUE <span class="box"></span>
    WED <span class="box"></span>
    THU <span class="box"></span>
    FRI <span class="box"></span>
    SAT <span class="box"></span>
  </div>

  <p class="notice">If you are unable to keep your appointment, kindly give 48 hours notice</p>
</section>

</body>
</html>
```